MS word document templates for consultancy

I need the following templates for my business using my logo as branding.

- General report template
- Letter head template
- Tender proposal template

The templates should be sleek and with minimal colors, but with a small amount of green and grey where appropriate (as per attached logo and email signature). Font should be consistent with the text in the email signature.

```html
<!DOCTYPE html>
<html lang="en">
<head>
<meta charset="utf-8">
<title>Stridewell Group Letterhead</title>
<link href="https://fonts.googleapis.com/css2?family=Aleo:wght@400;700&display=swap" rel="stylesheet">
<style>
  :root {
    --brand-green: #2a9444;
    --margin-grey: #d9d9d9;
    --paper: #ffffff;
    --ink: #1a1a1a;
  }
  html, body {
    margin: 0;
    padding: 0;
    width: 848px;
    height: 1200px;
    overflow: hidden;
    background: var(--paper);
  }
  .letterhead {
    position: relative;
    width: 848px;
    height: 1200px;
    background: var(--paper);
    font-family: "Aleo", Georgia, serif;
  }
  .side-band {
    position: absolute;
    left: 0;
    top: 0;
    width: 59px;
    height: 1200px;
    background: var(--margin-grey);
  }
  .header-tab {
    position: absolute;
    left: 0;
    top: 96px;
    width: 95px;
    height: 60px;
    background: var(--brand-green);
  }
  .company-name {
    position: absolute;
    left: 118px;
    top: 100px;
    margin: 0;
    font-size: 42px;
    font-weight: 400;
    line-height: 52px;
    color: var(--ink);
    white-space: nowrap;
  }
  .sender {
    position: absolute;
    right: 84px;
    top: 108px;
    text-align: right;
    color: var(--brand-green);
    font-size: 21px;
    letter-spacing: 3px;
    line-height: 28px;
  }
  .sender-name {
    margin: 0;
    font-weight: 700;
  }
  .sender-role {
    margin: 0;
    font-weight: 400;
  }
  .contact {
    position: absolute;
    right: 84px;
    top: 1076px;
    margin: 0;
    color: var(--brand-green);
    font-size: 14px;
    letter-spacing: 2.6px;
    white-space: nowrap;
  }
  .contact-label {
    font-weight: 700;
  }
</style>
</head>
<body>
  <div class="letterhead">
    <div class="side-band"></div>
    <div class="header-tab"></div>
    <p class="company-name">Stridewell Group</p>
    <div class="sender">
      <p class="sender-name">Daniel Ashcombe</p>
      <p class="sender-role">Managing Director</p>
    </div>
    <p class="contact"><span class="contact-label">Phone:</span> 0400 555 193</p>
  </div>
</body>
</html>
```